R7M Horizon Business Card Design

We need a business card created for our New Business "R7M Horizon"<br/><br/>The business card design is up to you however the following information must be on the business card:<br/><br/>Front of the business card -<br/>Email :darrenp@r7mhorizon.nz<br/>Mobile: +64 (0) 22 4870 619<br/>Website: www.r7mhorizon.nz<br/>Card Owner Name: Darren Paltrow<br/>Company Title: Business Development Manager<br/>Slogan: "Bold ideas, FINE finish". <br/>Logo On the front attached to the design brief<br/><br/>On the back: <br/>Space on the back for 4 more versions of the logo across the bottom of the card indicating different subsidiary brands - R7M Coffee, R7M Arts, R7M ?? (The card will be used for all of these brands - We Will add the extra subsidiary logos to the design once the design is finished (We are a graphics design team). <br/><br/>Other than that we want a premium feeling logo that remains universally usable depending on the business entity that we are using the card for. The use of bright bold colours would be great but we still want the card to feel premium.
Target Market(s)
Gift Design and Manufacturing Companies
Contact Information for Business Card
Front of the business card -
Email :darrenp@r7mhorizon.nz
Mobile: +64 (0) 22 4870 619
Website: www.r7mhorizon.nz
Card Owner Name: Darren Paltrow
Company Title: Business Development Manager
Slogan: "Bold ideas, FINE finish".
Logo On the front attached to the design brief

```html
<!DOCTYPE html>
<html lang="en">
<head>
<meta charset="UTF-8">
<title>R7M Horizon Business Card</title>
<link href="https://fonts.googleapis.com/css2?family=Ubuntu:wght@400;500;700&display=swap" rel="stylesheet">
<style>
  :root {
    --stage: #1c1c1d;
    --card: #232324;
    --card-deep: #1f1f20;
    --brand-blue: #3a4fb5;
    --ring-faint: #262a3f;
    --mark-faint: #2e2e30;
    --text-light: #f2f2f2;
    --rule: #d8d8d8;
  }
  * { box-sizing: border-box; margin: 0; padding: 0; }
  html, body {
    width: 1200px; height: 900px; overflow: hidden;
    background: var(--stage);
    font-family: "Ubuntu", sans-serif;
  }
  .stage { position: relative; width: 1200px; height: 900px; }
  .card {
    position: absolute; left: 250px; width: 700px; height: 400px;
    background: var(--card); overflow: hidden;
    box-shadow: 0 10px 30px rgba(0,0,0,.45);
  }
  .card--back { top: 30px; background: var(--card-deep); }
  .card--front { top: 470px; }

  /* back */
  .back-ring {
    position: absolute; left: 200px; top: 50px; width: 300px; height: 300px;
    border: 5px solid var(--ring-faint); border-radius: 50%;
  }
  .back-name {
    position: absolute; left: 0; right: 0; top: 178px; text-align: center;
    font-size: 36px; font-weight: 700; color: var(--mark-faint); letter-spacing: 1px;
    white-space: nowrap;
  }

  /* front */
  .brand-name {
    position: absolute; left: 40px; top: 152px;
    font-size: 40px; font-weight: 700; color: var(--brand-blue); letter-spacing: .5px;
    white-space: nowrap;
  }
  .rule { position: absolute; width: 2px; background: var(--rule); }
  .rule--top { left: 340px; top: 78px; height: 44px; }
  .rule--bottom { left: 340px; top: 138px; height: 80px; }
  .person { position: absolute; left: 362px; top: 74px; }
  .person-name {
    font-size: 27px; font-weight: 700; color: var(--brand-blue);
    text-transform: uppercase; letter-spacing: 1px; line-height: 1.05;
  }
  .person-title { font-size: 18px; color: var(--text-light); margin-top: 3px; }
  .contacts { position: absolute; left: 356px; top: 140px; list-style: none; }
  .contacts li {
    display: flex; align-items: center; gap: 10px;
    font-size: 19px; color: var(--text-light); height: 26px; letter-spacing: .5px;
  }
  .contacts svg { width: 18px; height: 18px; flex: none; }
  .slogan-band {
    position: absolute; left: 0; right: 0; top: 318px; height: 40px;
    background: var(--brand-blue); color: var(--text-light);
    display: flex; align-items: center; justify-content: center;
    font-size: 21px; letter-spacing: .5px;
  }
</style>
</head>
<body>
<main class="stage">
  <section class="card card--back" aria-label="Card back">
    <div class="back-ring"></div>
    <div class="back-name">R7M Horizon</div>
  </section>

  <section class="card card--front" aria-label="Card front">
    <div class="brand-name">R7M Horizon</div>
    <span class="rule rule--top"></span>
    <span class="rule rule--bottom"></span>
    <div class="person">
      <h1 class="person-name">Darren Paltrow</h1>
      <p class="person-title">Business Development Manager</p>
    </div>
    <ul class="contacts">
      <li>
        <svg viewBox="0 0 24 24" fill="none" stroke="#3a4fb5" stroke-width="1.8" stroke-linecap="round" stroke-linejoin="round"><path d="M22 16.9v3a2 2 0 0 1-2.2 2 19.8 19.8 0 0 1-8.6-3.1 19.5 19.5 0 0 1-6-6A19.8 19.8 0 0 1 2.1 4.2 2 2 0 0 1 4.1 2h3a2 2 0 0 1 2 1.7c.1 1 .4 1.9.7 2.8a2 2 0 0 1-.5 2.1L8 9.8a16 16 0 0 0 6 6l1.3-1.3a2 2 0 0 1 2.1-.4c.9.3 1.8.6 2.8.7a2 2 0 0 1 1.7 2z"/></svg>
        +64 (0) 22 4870 619
      </li>
      <li>
        <svg viewBox="0 0 24 24" fill="none" stroke="#3a4fb5" stroke-width="1.8" stroke-linejoin="round"><rect x="2" y="5" width="20" height="14" rx="1"/><path d="M2 6l10 7 10-7"/></svg>
        darrenp@r7mhorizon.nz
      </li>
      <li>
        <svg viewBox="0 0 24 24" fill="none" stroke="#3a4fb5" stroke-width="1.8"><circle cx="12" cy="12" r="10"/><path d="M2 12h20M12 2a15 15 0 0 1 0 20M12 2a15 15 0 0 0 0 20"/></svg>
        www.r7mhorizon.nz
      </li>
    </ul>
    <div class="slogan-band">Bold ideas, FINE finish</div>
  </section>
</main>
</body>
</html>
```